Shopify Web-Page "Tiny-ThreadDays

We are building a new business in Switzerland offering premium sewing holiday camps for kids aged 9–14. In enclosed brief outlines our requirements for a complete Shopify homepage design and a multilingual logo creation.
Domains: tiny-threaddays.ch ; tiny-giornifilo.ch ; tiny-fadentage.ch

Project Overview
We are looking for:
1. A modern, fully designed Shopify homepage in English using standard Shopify content blocks (no custom coding), which we can later update ourselves. Supporting Multilanguage (EN, German, Italian).

2. A logo design that includes the brand identity and communicates our multilingual, creative, and child-focused positioning.

All details in enclosed

```html
<!DOCTYPE html>
<html lang="en">
<head>
<meta charset="utf-8">
<title>Tiny-ThreadDays – Creative Holiday Sewing Camps</title>
<link href="https://fonts.googleapis.com/css2?family=Playfair+Display:ital,wght@0,400;1,400&family=Jost:wght@300;400;500;600&display=swap" rel="stylesheet">
<style>
:root{
  --coral:#f36b61;
  --coral-dark:#e85a50;
  --blush:#fdeeed;
  --navy:#1d2a3b;
  --ink:#222222;
  --muted:#555555;
  --white:#ffffff;
}
*{box-sizing:border-box;margin:0;padding:0}
html,body{width:1200px;height:4612px;overflow:hidden}
body{position:relative;font-family:"Jost",sans-serif;color:var(--ink);background:var(--white)}
.abs{position:absolute}
.serif{font-family:"Playfair Display",serif;font-style:italic;font-weight:400;text-transform:uppercase;letter-spacing:-0.5px}
.btn{position:absolute;display:flex;align-items:center;justify-content:center;background:var(--coral);color:var(--white);border-radius:30px;font-size:14px;font-weight:500}

/* header */
.site-header{left:0;top:0;width:1200px;height:161px;background:var(--coral)}
.lang{left:111px;top:43px;width:100px;height:32px;background:var(--white);border-radius:16px;font-size:12px;display:flex;align-items:center;padding:0 14px;justify-content:space-between}
.brand{left:400px;top:48px;width:400px;text-align:center;color:var(--white);font-family:"Jost",sans-serif;font-weight:300;font-size:32px;letter-spacing:1px}
.cart{left:1051px;top:41px;width:36px;height:36px;border-radius:50%;background:var(--white);display:flex;align-items:center;justify-content:center}
.nav{top:119px;left:0;width:1200px;display:flex;justify-content:center;gap:0;font-size:14px;color:var(--white)}
.nav span{position:absolute;top:0;transform:translateX(-50%)}

/* hero */
.hero{left:0;top:161px;width:1200px;height:543px;background:linear-gradient(110deg,#6b3a8a 0%,#9c3fd8 30%,#b7865a 60%,#d8a35d 80%,#2f7a4f 100%)}
.hero-panel{left:111px;top:278px;width:486px;height:310px;background:rgba(20,28,45,.88);border-radius:18px;text-align:center;color:var(--white)}
.hero-panel h1{position:absolute;top:38px;left:0;width:100%;font-size:40px;line-height:48px}
.hero-panel h1 .plain{font-style:normal;color:var(--white)}
.hero-panel h1 .accent{color:var(--coral)}
.hero-panel p{position:absolute;top:186px;width:100%;font-size:17px}

/* offerings */
.section-title{font-size:40px;color:var(--ink)}
.card{width:235px;height:362px;top:856px;border:2px solid #f5b3ad;border-radius:16px;background:var(--white)}
.card .thumb{position:absolute;left:14px;top:14px;width:203px;height:211px;border-radius:12px}
.card .name{position:absolute;left:16px;top:240px;font-size:16px;color:var(--muted)}
.card .price{position:absolute;left:16px;top:266px;font-size:21px;font-weight:600}
.card .btn{left:14px;top:306px;width:203px;height:41px}

/* split cards */
.split{left:111px;width:976px;height:419px;background:var(--white);border-radius:28px;box-shadow:0 8px 30px rgba(0,0,0,.08);overflow:hidden}
.split .photo{position:absolute;left:0;top:0;width:487px;height:100%}
.split .body{position:absolute;left:556px;width:380px}
.split p{font-size:15px;line-height:30px;color:var(--muted);text-align:justify}

/* why */
.why{left:0;top:1850px;width:1200px;height:473px;background:var(--blush)}
.why ul{list-style:none;position:absolute;left:111px;top:130px;width:410px}
.why li{position:relative;padding-left:34px;font-size:15px;line-height:30px;color:var(--muted);text-align:justify}
.why li svg{position:absolute;left:0;top:8px}
.why .photo{left:600px;top:63px;width:487px;height:345px;border-radius:22px}

/* how */
.how{left:0;top:2323px;width:1200px;height:466px;background:var(--coral)}
.how h2{position:absolute;top:52px;width:100%;text-align:center;color:var(--white);font-size:40px}
.step{position:absolute;top:149px;width:186px;text-align:center;color:var(--white)}
.step .ring{width:110px;height:110px;margin:0 auto;border-radius:50%;background:rgba(255,255,255,.25);display:flex;align-items:center;justify-content:center}
.step .core{width:86px;height:86px;border-radius:50%;background:var(--coral-dark);border:2px solid rgba(255,255,255,.7);display:flex;align-items:center;justify-content:center}
.step h3{margin-top:24px;font-size:16px;font-weight:400;line-height:25px}
.step p{font-size:12px;line-height:23px;margin-top:2px;opacity:.95}

/* faq */
.faq-item{left:285px;width:629px;height:52px;background:var(--blush);border:1px solid #f3c3bf;border-radius:6px;display:flex;align-items:center;padding:0 22px;font-size:14px}
.faq-item .num{width:40px}
.faq-item svg{margin-left:auto}

/* footer */
.footer{left:0;top:3994px;width:1200px;height:618px;background:var(--navy);color:var(--white)}
.footer h2{position:absolute;top:46px;width:100%;text-align:center;font-size:40px}
.footer .lead{position:absolute;top:108px;width:100%;text-align:center;font-size:16px}
.signup{left:417px;top:157px;width:366px;height:44px;border-radius:22px;background:var(--coral);display:flex;align-items:center;padding:0 24px;font-size:13px;justify-content:space-between}
.rule{left:111px;top:245px;width:978px;height:1px;background:rgba(255,255,255,.15)}
.col h4{font-family:"Playfair Display",serif;font-style:italic;font-weight:400;text-transform:uppercase;color:var(--coral);font-size:20px;margin-bottom:16px}
.col a,.col div{display:block;font-size:14px;line-height:36px;color:var(--white);text-decoration:none}
.col a.u{text-decoration:underline}
.foot-brand{left:806px;top:360px;width:283px;text-align:center;font-size:40px;font-weight:300}
.copy{top:574px;width:100%;text-align:center;font-size:14px}
</style>
</head>
<body>

<header class="abs site-header">
  <div class="abs lang"><span>English</span><span>⇕</span></div>
  <div class="abs brand">Tiny-ThreadDays</div>
  <div class="abs cart">
    <svg width="14" height="14" viewBox="0 0 24 24"><path d="M2 4h3l3 11h11l3-8H7" fill="none" stroke="#f36b61" stroke-width="2.5"/><circle cx="9" cy="20" r="2" fill="#f36b61"/><circle cx="18" cy="20" r="2" fill="#f36b61"/></svg>
  </div>
  <nav class="abs nav">
    <span style="left:295px">Home</span>
    <span style="left:394px">About Us</span>
    <span style="left:530px">Why Choose Us?</span>
    <span style="left:681px">How It Works</span>
    <span style="left:788px">FAQ</span>
    <span style="left:886px">Contact Us</span>
  </nav>
</header>

<section class="abs hero" role="img" aria-label="Photo of a young girl sewing colourful fabric at a sewing machine"></section>
<div class="abs hero-panel">
  <h1 class="serif"><span class="plain">Creative Holiday</span><br><span class="accent">Sewing Camps for<br>Kids (Ages 9–14)</span></h1>
  <p>Fun • Fashion • Friendship — in Zurich and beyond</p>
  <div class="btn" style="left:167px;top:245px;width:150px;height:38px">Book a Camp</div>
</div>

<h2 class="abs serif section-title" style="left:111px;top:774px">Our Upcoming Camp Offerings</h2>

<div class="abs card" style="left:111px">
  <div class="thumb" role="img" aria-label="Photo of children sewing with their teacher" style="background:linear-gradient(160deg,#8a7260,#c98f8a,#d9c2b0)"></div>
  <div class="name">Spring Camps</div><div class="price">$45.00</div><div class="btn">Add to Cart</div>
</div>
<div class="abs card" style="left:358px">
  <div class="thumb" role="img" aria-label="Photo of children crafting at a table" style="background:linear-gradient(160deg,#3f5a4b,#b48a6a,#d65a52)"></div>
  <div class="name">Summer Camps</div><div class="price">$45.00</div><div class="btn">Add to Cart</div>
</div>
<div class="abs card" style="left:605px">
  <div class="thumb" role="img" aria-label="Photo of a sewing machine stitching blue fabric" style="background:linear-gradient(160deg,#c9b8a8,#2b4a8f,#e0507a)"></div>
  <div class="name">Spring Camps</div><div class="price">$45.00</div><div class="btn">Add to Cart</div>
</div>
<div class="abs card" style="left:852px">
  <div class="thumb" role="img" aria-label="Photo of children working with colourful fabrics" style="background:linear-gradient(160deg,#4a4a5a,#a45f4f,#5a6fb0)"></div>
  <div class="name">Summer Camps</div><div class="price">$45.00</div><div class="btn">Add to Cart</div>
</div>

<section class="abs split" style="top:1311px">
  <div class="photo" role="img" aria-label="Photo of children cutting colourful felt shapes" style="background:linear-gradient(150deg,#6a6b70,#c8a48a,#d84a4a,#3d7fc0)"></div>
  <div class="body" style="top:38px">
    <h2 class="serif" style="font-size:40px">About Us</h2>
    <p style="margin-top:16px">We are building a new business in Switzerland offering premium sewing holiday camps for kids aged 9—14.</p>
    <p style="margin-top:30px">Ut enim ad minima veniam, quis nostrum exercitationem ullam corporis suscipit laboriosam, nisi ut aliquid ex ea commodi</p>
  </div>
  <div class="btn" style="left:556px;top:351px;width:150px;height:38px">Book a Camp</div>
</section>

<section class="abs why">
  <h2 class="serif section-title" style="position:absolute;left:111px;top:60px">Why Choose Us</h2>
  <ul>
    <li><svg width="15" height="15" viewBox="0 0 15 15"><rect width="15" height="15" rx="3" fill="#f36b61"/><path d="M4 7.5l2.5 2.5L11 5" stroke="#fff" stroke-width="2" fill="none"/></svg>Small groups &amp; personalized attention</li>
    <li><svg width="15" height="15" viewBox="0 0 15 15"><rect width="15" height="15" rx="3" fill="#f36b61"/><path d="M4 7.5l2.5 2.5L11 5" stroke="#fff" stroke-width="2" fill="none"/></svg>Multilingual supervision (DE / EN / IT)</li>
    <li><svg width="15" height="15" viewBox="0 0 15 15"><rect width="15" height="15" rx="3" fill="#f36b61"/><path d="M4 7.5l2.5 2.5L11 5" stroke="#fff" stroke-width="2" fill="none"/></svg>High-quality fabrics &amp; top-quality sewing machines (Lindenau)</li>
    <li><svg width="15" height="15" viewBox="0 0 15 15"><rect width="15" height="15" rx="3" fill="#f36b61"/><path d="M4 7.5l2.5 2.5L11 5" stroke="#fff" stroke-width="2" fill="none"/></svg>Encouragement of creativity, self-confidence, and fine motor skills</li>
    <li><svg width="15" height="15" viewBox="0 0 15 15"><rect width="15" height="15" rx="3" fill="#f36b61"/><path d="M4 7.5l2.5 2.5L11 5" stroke="#fff" stroke-width="2" fill="none"/></svg>Safe, loving environment in Zurich, various places easy to reach</li>
    <li><svg width="15" height="15" viewBox="0 0 15 15"><rect width="15" height="15" rx="3" fill="#f36b61"/><path d="M4 7.5l2.5 2.5L11 5" stroke="#fff" stroke-width="2" fill="none"/></svg>Pick-up Service from the Main-Station</li>
  </ul>
  <div class="abs photo" role="img" aria-label="Photo of hands threading needles among spools of colourful thread" style="background:linear-gradient(140deg,#3a2a22,#8a5a3a,#4aa58a,#d8c8b0)"></div>
</section>

<section class="abs how">
  <h2 class="serif">How the Camp Works</h2>
  <div class="step" style="left:107px">
    <div class="ring"><div class="core"><svg width="40" height="40" viewBox="0 0 40 40" fill="none" stroke="#fff" stroke-width="2"><rect x="14" y="6" width="12" height="28" rx="2"/><path d="M14 12h5M14 18h5M14 24h5M14 30h5"/></svg></div></div>
    <h3>PROJECT SELECTION</h3>
    <p>Your child chooses their own model based on previously produced clothing items and sewing patterns.</p>
  </div>
  <div class="step" style="left:307px">
    <div class="ring"><div class="core"><svg width="40" height="40" viewBox="0 0 40 40" fill="none" stroke="#fff" stroke-width="2"><rect x="8" y="8" width="18" height="22"/><circle cx="24" cy="30" r="4"/><circle cx="32" cy="30" r="4"/><path d="M26 27l8-14M30 27l-6-14"/></svg></div></div>
    <h3>FABRIC SELECTION</h3>
    <p>High-quality fabrics are available.</p>
  </div>
  <div class="step" style="left:507px">
    <div class="ring"><div class="core"><svg width="40" height="40" viewBox="0 0 40 40" fill="none" stroke="#fff" stroke-width="2"><path d="M8 32h26M10 32V12h20v8H16v12"/><path d="M22 20v6"/></svg></div></div>
    <h3>SEWING MACHINE<br>OPERATION</h3>
    <p>Learn how to use a sewing machine</p>
  </div>
  <div class="step" style="left:706px">
    <div class="ring"><div class="core"><svg width="40" height="40" viewBox="0 0 40 40" fill="none" stroke="#fff" stroke-width="2"><path d="M10 32L32 8"/><ellipse cx="30" cy="10" rx="2" ry="3" transform="rotate(45 30 10)"/><path d="M12 20c4 0 6 4 10 4"/></svg></div></div>
    <h3>SEWING &amp; REFINING</h3>
    <p>Step by step to the goal with professional guidance</p>
  </div>
  <div class="step" style="left:906px">
    <div class="ring"><div class="core"><svg width="40" height="40" viewBox="0 0 40 40" fill="#fff"><path d="M16 6h8l-2 8 10 20H8l10-20z"/></svg></div></div>
    <h3>SHOWTIME!</h3>
    <p>Fashion show or photo shoot at the end of the week</p>
  </div>
</section>

<section class="abs split" style="top:2907px">
  <div class="photo" role="img" aria-label="Photo of a girl sewing green felt at a table" style="background:linear-gradient(150deg,#7a5a3a,#d8c4a8,#e8e0d8,#5a8a3a)"></div>
  <div class="body" style="top:36px">
    <h2 class="serif" style="font-size:40px;line-height:52px">Ready to Make Your Child’s Holiday Unforgettable?</h2>
    <p style="margin-top:14px">Ut enim ad minima veniam, quis nostrum exercitationem ullam corporis</p>
  </div>
  <div class="btn" style="left:556px;top:332px;width:218px;height:38px">Book Your Camp Today</div>
</section>

<h2 class="abs serif section-title" style="left:0;top:3410px;width:1200px;text-align:center">Frequently Asked Questions</h2>
<div class="abs faq-item" style="top:3489px"><span class="num">01)</span>Does my child need any prior knowledge?<svg width="14" height="14" viewBox="0 0 14 14"><rect width="14" height="14" rx="2" fill="#222"/><path d="M7 3v8M3 7h8" stroke="#fff" stroke-width="2"/></svg></div>
<div class="abs faq-item" style="top:3561px"><span class="num">02)</span>How does the pick-up service work?<svg width="14" height="14" viewBox="0 0 14 14"><rect width="14" height="14" rx="2" fill="#222"/><path d="M7 3v8M3 7h8" stroke="#fff" stroke-width="2"/></svg></div>
<div class="abs faq-item" style="top:3633px"><span class="num">03)</span>How many items of clothing are produced?<svg width="14" height="14" viewBox="0 0 14 14"><rect width="14" height="14" rx="2" fill="#222"/><path d="M7 3v8M3 7h8" stroke="#fff" stroke-width="2"/></svg></div>
<div class="abs faq-item" style="top:3705px"><span class="num">04)</span>How does pick-up service work?<svg width="14" height="14" viewBox="0 0 14 14"><rect width="14" height="14" rx="2" fill="#222"/><path d="M7 3v8M3 7h8" stroke="#fff" stroke-width="2"/></svg></div>
<div class="abs faq-item" style="top:3777px"><span class="num">05)</span>What should my child bring?<svg width="14" height="14" viewBox="0 0 14 14"><rect width="14" height="14" rx="2" fill="#222"/><path d="M7 3v8M3 7h8" stroke="#fff" stroke-width="2"/></svg></div>
<div class="abs faq-item" style="top:3849px"><span class="num">06)</span>What if my child has never used a sewing machine?<svg width="14" height="14" viewBox="0 0 14 14"><rect width="14" height="14" rx="2" fill="#222"/><path d="M7 3v8M3 7h8" stroke="#fff" stroke-width="2"/></svg></div>

<footer class="abs footer">
  <h2 class="serif">Join Our Newsletter</h2>
  <p class="lead">Quis autem vel eum iure reprehenderit qui in ea voluptate velit esse quam nihil molestiae</p>
  <div class="abs signup"><span>Email Address</span><span>→</span></div>
  <div class="abs rule"></div>
  <div class="abs col" style="left:111px;top:288px">
    <h4>Quick Links</h4>
    <a>Home</a><a>About Us</a><a>Why Choose Us?</a><a>How It Works</a><a>FAQ</a><a>Contact Us</a>
  </div>
  <div class="abs col" style="left:317px;top:288px">
    <h4>Contact Info</h4>
    <div>Tiny-ThreadDays GmbH, Postfach 5678,</div><div>8003 Zürich, Switzerland</div><div>&nbsp;</div>
    <div>hello@tiny-threaddays.ch</div><div>+41 44 000 00 00</div>
  </div>
  <div class="abs col" style="left:636px;top:288px">
    <h4>Follow Us</h4>
    <a class="u">Community</a><a class="u">Photo Diary</a><a class="u">Network</a><a class="u">Video Corner</a>
  </div>
  <div class="abs foot-brand">Tiny-ThreadDays</div>
  <div class="abs copy">(C) Copyright 2025 | All Right Reserved</div>
</footer>

</body>
</html>
```